Hardcore nerd needs to stand out in a sea of dull Defence business cards

Wombarra Devices is a new Australian consulting engineering company that turns research and theory into practical systems. No evangelistic fluff, just mathematics and physics into electronic and optical circuits for consumer products, scientific research or Defence applications.

We already have a recognised logo (provided) which is often dark blue/black on a light background but we're open to other combinations. (Us engineers tend to have limited aesthetic imagination :)

Some of our recent products have included:
* Instrumentation for electrical testing,
* Radar jammers,
* GPS antenna design,
* Satellite tracking systems,
* High power lasers

We're open to both single and double-sided designs - happy to be convinced either way.

P.S. Another group is working on the web page, so - alas - our web site is currently of no use for images/ideas...

Target Market(s)

Engineering managers,
Scientists

Contact Information for Business Card

Dr Colin Harte
R&D Engineer

colin@wombarradevices.com.au
0427 563 710

PO Box XXX (to be confirmed)
Kelsby ACT 2917
Australia

Font styles to use
Serif
Sans Serif

Colors

Designer to choose colors to be used in the design.

Requirements
Must have
• My contact details!
• I've had many (great) "bold and plain" designs submitted already, so feel free to be artistically creative :)
• Happy to take advice re fonts/colours/printability etc.
Nice to have
• I'm not sure if "lists" are more at home on a CV than a business card, but representative services include:
• Applied electromagnetics
• RF and high speed electronics
• Signal and image processing
• Electro-optical and laser systems
• Concept-to-prototype design services
• If you're considering double sided cards, then often measuring/alignment grids/rulers feature on the back of similar cards.
• e.g. https://www.veltranoptics.example/newgrouppage9.cfm?objectgroup_id=4183
• https://www.veltranoptics.example/newgrouppage9.cfm?objectgroup_ID=4185
• ..or even a "Smith chart" (google will return lots)
• Generic images to represent a capability might work - googling images associated with keyword for each of these areas might help:
• - "passive radar", "phased array", "fdtd", "vircator"
• RF and high speed electronic design
• - "smith chart", "microstrip circuits", "dimensioned drawing", "electronic schematic"
• - "dft", "iir filter"
• - "optical cavity". "laser energy level diagram"
• Background/watermarked images outlines/wireframes/schematics would probably look OK.
Should not have
• If a list of projects/services is provided, it is important not to make the client feel that this is "all" the company can do. Engineering design is a creative discipline (like graphics :)
• Please, no stock "military" snaps like planes, missiles, etc!

```html
<!DOCTYPE html>
<html lang="en">
<head>
<meta charset="utf-8">
<title>Wombarra Devices – Business Card</title>
<link rel="stylesheet" href="https://fonts.googleapis.com/css2?family=Lato:wght@400;700;900&display=swap">
<style>
  :root {
    --navy: #0c2366;
    --white: #ffffff;
    --backdrop: #d9d9db;
    --ink-soft: #e8ecf5;
  }
  * { box-sizing: border-box; margin: 0; padding: 0; }
  html, body {
    width: 1200px; height: 900px; overflow: hidden;
    background: var(--backdrop);
    font-family: "Lato", Arial, sans-serif;
  }
  .sheet {
    width: 1200px; height: 900px;
    display: flex; flex-direction: column; align-items: center; justify-content: center;
    gap: 40px;
  }
  .card {
    position: relative;
    width: 700px; height: 400px;
    border-radius: 26px;
    overflow: hidden;
    background: var(--navy);
    color: var(--white);
  }

  /* Front */
  .card-front .base-band {
    position: absolute; left: 0; right: 0; bottom: 0; height: 88px;
    background: var(--white);
  }
  .brand {
    position: absolute; left: 0; right: 0; top: 120px;
    display: flex; align-items: center; justify-content: center; gap: 18px;
  }
  .brand-dot {
    width: 64px; height: 64px; border-radius: 50%;
    background: var(--white);
  }
  .brand-name {
    font-weight: 900; font-size: 38px; letter-spacing: 1px;
    text-transform: uppercase; color: var(--white);
  }
  .services {
    position: absolute; left: 70px; right: 40px; bottom: 100px;
    display: grid; grid-template-columns: 1fr 1fr; column-gap: 24px; row-gap: 2px;
    list-style: none; font-size: 17px; color: var(--white);
  }
  .services li::before { content: "• "; }

  /* Back */
  .card-back .base-band {
    position: absolute; left: 0; right: 0; bottom: 0; height: 48px;
    background: var(--white);
  }
  .card-back .corner-sweep {
    position: absolute; right: -60px; top: -60px; width: 200px; height: 200px;
    background: var(--white); transform: rotate(45deg) translate(60px, -40px);
  }
  .emblem-disc {
    position: absolute; right: 40px; top: 40px;
    width: 290px; height: 290px; border-radius: 50%;
    background: var(--white);
  }
  .contact {
    position: absolute; left: 50px; top: 70px;
    list-style: none; font-size: 17px; line-height: 1.35;
  }
  .contact li { display: flex; align-items: center; gap: 8px; }
  .contact svg { width: 13px; height: 13px; fill: var(--white); flex: none; }
  .postal {
    position: absolute; left: 50px; top: 185px;
    font-size: 17px; line-height: 1.3; font-style: normal;
  }
  .person {
    position: absolute; left: 50px; top: 268px;
  }
  .person-name { font-weight: 900; font-size: 22px; text-transform: uppercase; letter-spacing: .3px; }
  .person-role { font-size: 16px; color: var(--ink-soft); }
</style>
</head>
<body>
<main class="sheet">

  <section class="card card-front" aria-label="Card front">
    <div class="brand">
      <span class="brand-dot"></span>
      <span class="brand-name">Wombarra Devices</span>
    </div>
    <ul class="services">
      <li>Applied electromagnetics</li>
      <li>RF and high speed electronics</li>
      <li>Signal and image processing</li>
      <li>Electro-optical and laser systems</li>
    </ul>
    <div class="base-band"></div>
  </section>

  <section class="card card-back" aria-label="Card back">
    <div class="corner-sweep"></div>
    <div class="emblem-disc"></div>
    <ul class="contact">
      <li>
        <svg viewBox="0 0 16 16"><path d="M3 1l3 3-1.5 2a9 9 0 0 0 5.5 5.5L12 10l3 3-2 2C6 15 1 10 1 3z"/></svg>
        0427 563 710
      </li>
      <li>
        <svg viewBox="0 0 16 16"><path d="M1 3h14v10H1zM2 4l6 5 6-5v-0.2H2z" fill-rule="evenodd"/></svg>
        colin@wombarradevices.com.au
      </li>
      <li>
        <svg viewBox="0 0 16 16"><circle cx="8" cy="8" r="7"/></svg>
        www.wombarradevices.com.au
      </li>
    </ul>
    <address class="postal">
      PO Box XXX<br>
      Kelsby ACT 2917, Australia
    </address>
    <div class="person">
      <p class="person-name">Dr Colin Harte</p>
      <p class="person-role">R&amp;D Engineer</p>
    </div>
    <div class="base-band"></div>
  </section>

</main>
</body>
</html>
```